Business Card for a Dental Office

The design should communicate integrity, quality and reliability. We also want the card look elegant, simple, but still stand out, different from the traditional-dental-office business card.

Industry/Entity Type

Business

```html
<!DOCTYPE html>
<html lang="en">
<head>
<meta charset="utf-8">
<title>Harbor Dental Studio – Business Card</title>
<link href="https://fonts.googleapis.com/css2?family=Oswald:wght@600&family=Arimo:wght@400;700&display=swap" rel="stylesheet">
<style>
  :root {
    --stage: #2e2e30;
    --ink: #111111;
    --paper: #ffffff;
    --gold: #c9a227;
    --gold-light: #f2de2a;
    --gold-dark: #8e7315;
    --text-grey: #6b6b6b;
    --soft-white: #e9e9e9;
  }
  * { box-sizing: border-box; margin: 0; padding: 0; }
  html, body { width: 1200px; height: 950px; overflow: hidden; }
  body {
    background: var(--stage);
    font-family: "Arimo", Arial, sans-serif;
    display: flex; flex-direction: column; align-items: center; justify-content: center;
    gap: 50px;
  }
  .card {
    position: relative;
    width: 700px; height: 400px;
    border-radius: 4px;
    overflow: hidden;
    box-shadow: 0 18px 40px rgba(0,0,0,.45);
  }
  .brand {
    display: flex; align-items: center; gap: 14px;
  }
  .brand-mark { width: 22px; height: 22px; flex: none; }
  .brand-name {
    font-family: "Oswald", "Arial Narrow", sans-serif;
    font-weight: 600; font-size: 34px; letter-spacing: .5px;
    text-transform: uppercase; line-height: 1;
  }

  /* Front */
  .card-front { background: var(--ink); }
  .card-front .brand { position: absolute; left: 150px; top: 165px; }
  .card-front .brand-mark { background: var(--gold); }
  .card-front .brand-name { color: var(--paper); }
  .card-front .website {
    position: absolute; left: 0; right: 0; top: 290px; text-align: center;
    padding-left: 140px;
    color: var(--soft-white); font-size: 15px; letter-spacing: 3px;
  }

  /* Back */
  .card-back { background: var(--paper); }
  .card-back .brand { position: absolute; left: 50px; top: 80px; }
  .card-back .brand-mark { background: var(--ink); }
  .card-back .brand-name { color: var(--ink); font-size: 30px; }

  .contact-list {
    position: absolute; left: 420px; top: 148px; list-style: none;
  }
  .contact-list li {
    display: flex; align-items: center; gap: 10px;
    font-size: 15px; color: var(--text-grey); height: 23px;
  }
  .contact-list svg { width: 14px; height: 14px; fill: var(--ink); flex: none; }

  .accent-band { position: absolute; top: 262px; left: 498px; right: 0; height: 14px; display: flex; }
  .accent-band .band-dark { width: 36px; background: var(--ink); }
  .accent-band .band-gap { width: 5px; background: var(--paper); }
  .accent-band .band-gold { flex: 1; background: linear-gradient(90deg, var(--gold-dark), var(--gold-light) 60%, var(--gold)); }

  .person { position: absolute; left: 120px; top: 285px; }
  .person-name { font-size: 20px; font-weight: 700; color: var(--ink); }
  .person-title { font-size: 16px; color: var(--gold); margin-top: 4px; }
  .person-address { font-size: 16px; color: var(--text-grey); margin-top: 4px; line-height: 1.35; font-style: normal; }
</style>
</head>
<body>
  <section class="card card-front" aria-label="Card front">
    <div class="brand">
      <span class="brand-mark"></span>
      <span class="brand-name">Harbor Dental Studio</span>
    </div>
    <p class="website">www.harbordentalstudio.com</p>
  </section>

  <section class="card card-back" aria-label="Card back">
    <div class="brand">
      <span class="brand-mark"></span>
      <span class="brand-name">Harbor Dental Studio</span>
    </div>

    <ul class="contact-list">
      <li>
        <svg viewBox="0 0 16 16" aria-hidden="true"><path d="M3 1h3l1.5 4-2 1.3a9 9 0 0 0 4.2 4.2L11 8.5l4 1.5v3a2 2 0 0 1-2 2A13 13 0 0 1 1 3a2 2 0 0 1 2-2z"/></svg>
        312 5540 7781
      </li>
      <li>
        <svg viewBox="0 0 16 16" aria-hidden="true"><path d="M4 0h8a1 1 0 0 1 1 1v14a1 1 0 0 1-1 1H4a1 1 0 0 1-1-1V1a1 1 0 0 1 1-1zm1 2v10h6V2zm3 11a1 1 0 1 0 0 2 1 1 0 0 0 0-2z"/></svg>
        312 6618 2094
      </li>
      <li>
        <svg viewBox="0 0 16 16" aria-hidden="true"><path d="M4 0h8v5H4zM1 6h14v8h-3v2H4v-2H1zm4 5v3h6v-3z"/></svg>
        312 5540 7790
      </li>
      <li>
        <svg viewBox="0 0 16 16" aria-hidden="true"><path d="M0 3h16v1L8 9 0 4zm0 3 8 5 8-5v7H0z"/></svg>
        mara@harbordentalstudio.com
      </li>
    </ul>

    <div class="accent-band" aria-hidden="true">
      <span class="band-dark"></span><span class="band-gap"></span><span class="band-gold"></span>
    </div>

    <div class="person">
      <p class="person-name">Mara Ellison</p>
      <p class="person-title">President</p>
      <address class="person-address">412 Linden Hollow Road<br>Maple Ridge, NY 10990</address>
    </div>
  </section>
</body>
</html>
```